Concierge Dental / Medical Supply Ordering Business - Sleek, Efficient, Professional, Elite

www.brantonkeelmedical.com - example website.

We are a concierge supply ordering business for medical and dental that provide DSO price savings on supplies while maintaining business autonomy and independence.

We want a very simple website that looks very professional says what we do and gives a very simple method to contact us & sign up as above.

Target Market(s)

Independent Dental and Medical Practices

Industry/Entity Type

Dental and Medical - healthcare

Coding

Coded - Design and coding required

Number of Pages Required

3 page

Font styles to use
Sans Serif

Colors
0054AA
0677BA
7BADD7
CADEEF
E8F1F8

Requirements
Must have
• Simple contact page, sleek efficient design, uncomplicated.
Nice to have
• Sign up page vs just a contact page.
Should not have
• Lots of pages, hard to navigate,

```html
<!DOCTYPE html>
<html lang="en">
<head>
<meta charset="utf-8">
<title>Brightpath Dental Supply</title>
<link href="https://fonts.googleapis.com/css2?family=Lato:wght@400;700;900&family=Roboto:wght@400;500&display=swap" rel="stylesheet">
<style>
:root{
  --blue:#0ba3e6;
  --blue-dark:#0677ba;
  --ink:#0b0b0b;
  --text:#555;
  --pale:#e4f5fb;
  --white:#fff;
}
*{margin:0;padding:0;box-sizing:border-box}
html,body{width:1200px;height:3083px;overflow:hidden}
body{position:relative;background:var(--white);font-family:'Lato',sans-serif;color:var(--ink)}
.abs{position:absolute}
.btn{position:absolute;display:flex;align-items:center;justify-content:center;background:var(--blue);color:var(--white);font:700 16px 'Lato',sans-serif;border-radius:3px;box-shadow:0 3px 0 var(--blue-dark)}
.hero-photo{left:0;top:0;width:1200px;height:720px;background:linear-gradient(100deg,#dfe6ea 0%,#e9eef1 45%,#cfd9df 70%,#b9c6cf 100%)}
.topbar{left:0;top:0;width:1200px;height:5px;background:#111}
.brand-box{left:111px;top:0;width:161px;height:154px;background:#111;border-radius:0 0 10px 10px;display:flex;flex-direction:column;align-items:center;justify-content:center;gap:10px}
.brand-box .mark{width:44px;height:44px;border:3px solid var(--blue);border-radius:6px}
.brand-box .name{color:var(--white);font:700 12px 'Lato',sans-serif;text-align:center}
.nav{top:96px;font:400 19px 'Lato',sans-serif;color:#111}
.welcome{left:111px;top:244px;font:900 55px/1 'Lato',sans-serif;color:var(--blue)}
.hero-title{left:111px;top:320px;font:900 76px/84px 'Lato',sans-serif;color:var(--ink);white-space:nowrap}
.h2{font:900 42px/1 'Lato',sans-serif;color:var(--ink)}
.h2 span{color:var(--blue)}
.about-photo{left:111px;top:824px;width:489px;height:532px;border-radius:16px;background:linear-gradient(135deg,#1b6fc4,#58b4ee 55%,#d5eefc);box-shadow:0 8px 20px rgba(0,0,0,.15)}
.about-copy{left:647px;top:919px;width:445px;display:flex;flex-direction:column;gap:27px}
.about-copy p{font:400 14.5px/27.5px 'Lato',sans-serif;color:var(--text)}
.about-copy .btn{position:static;width:120px;height:40px;margin-top:3px}
.lead{left:150px;width:900px;text-align:center;font:400 16px/30px 'Roboto',sans-serif;color:var(--text)}
.card{top:1627px;width:309px;height:465px;background:var(--white);border-radius:12px;box-shadow:0 4px 14px rgba(0,0,0,.1);border-bottom:3px solid var(--blue);overflow:hidden;text-align:center}
.card .photo{height:213px}
.card .icon{position:absolute;left:112px;top:173px;width:84px;height:84px;border-radius:50%;border:2px dotted var(--blue);padding:5px;background:var(--white)}
.card .icon div{width:100%;height:100%;border-radius:50%;background:var(--blue);display:flex;align-items:center;justify-content:center}
.card h3{position:absolute;left:0;top:284px;width:100%;font:400 20px 'Lato',sans-serif;color:var(--ink)}
.card p{position:absolute;top:322px;left:25px;right:25px;font:400 12.5px/26px 'Lato',sans-serif;color:var(--text)}
.card a{position:absolute;left:0;top:407px;width:100%;display:block;font:700 14px 'Lato',sans-serif;color:var(--blue);text-decoration:underline}
.arrow{width:38px;height:38px;border-radius:50%;top:1824px;display:flex;align-items:center;justify-content:center;font-size:18px}
.quote-band{left:0;top:2206px;width:1200px;height:600px;background:var(--pale)}
.quote{left:0;width:1200px;text-align:center;font:900 42px/56px 'Lato',sans-serif}
.footer-h{top:2796px;font:900 20px 'Lato',sans-serif;color:var(--white)}
.links{list-style:none;font:400 15px/31.5px 'Roboto',sans-serif;color:var(--white)}
.links li::before{content:"";display:inline-block;width:5px;height:5px;border-radius:50%;background:var(--blue);margin-right:14px;vertical-align:middle}
.field{left:848px;width:240px;height:36px;background:var(--white);border-radius:2px;font:400 11px 'Roboto',sans-serif;color:#444;display:flex;align-items:center;justify-content:space-between;padding:0 14px 0 22px}
</style>
</head>
<body>
<div class="abs hero-photo" role="img" aria-label="Doctor in white coat holding a stethoscope, with soft medical hexagon icons"></div>
<svg class="abs" style="left:0;top:560px" width="1200" height="200" viewBox="0 560 1200 200">
  <path d="M0 565 L252 670 L1100 580 L1200 565 L1200 760 L0 760Z" fill="#fff"/>
  <path d="M24 580 L252 720 L1100 580 L252 670Z" fill="#0ba3e6"/>
</svg>
<div class="abs topbar"></div>
<div class="abs brand-box"><div class="mark"></div><div class="name">Brightpath Dental Supply</div></div>
<div class="btn" style="left:968px;top:38px;width:120px;height:40px;font-size:16px">Contact Us</div>
<div class="abs nav" style="left:470px">Home</div>
<div class="abs nav" style="left:608px">About Us</div>
<div class="abs nav" style="left:774px">Practice Areas</div>
<div class="abs nav" style="left:983px">Testimonials</div>
<div class="abs welcome">WELCOME TO</div>
<div class="abs hero-title">BRIGHTPATH DENTAL<br>SUPPLY</div>
<div class="btn" style="left:111px;top:502px;width:120px;height:40px">Get Started</div>

<div class="abs about-photo" role="img" aria-label="Hospital corridor with a medical monitor in blue light"></div>
<div class="abs h2" style="left:647px;top:857px">ABOUT <span>US</span></div>
<div class="abs about-copy">
  <p>At vero eos et accusamus et iusto odio dignissimos ducimus qui blanditiis praesentium voluptatum deleniti atque corrupti quos dolores et quas molestias excepturi sint occaecati cupiditate non provident, similique sunt in culpa qui officia deserunt mollitia animi, id est laborum et dolorum fuga. Et harum quidem rerum facilis est et expedita distinctio. Nam libero tempore, cum soluta nobis est eligendi</p>
  <p>Temporibus autem quibusdam et aut officiis debitis aut rerum necessitatibus saepe eveniet ut et voluptates repudiandae sint et molestiae non recusandae. Itaque earum rerum hic tenetur a sapiente delectus, ut aut reiciendis voluptatibus maiores alias consequatur aut perferendis doloribus asperiores repellat.</p>
  <div class="btn">Read More</div>
</div>

<div class="abs h2" style="left:0;width:1200px;text-align:center;top:1466px">AREA OF <span>PRACTICE</span></div>
<p class="abs lead" style="top:1527px">At vero eos et accusamus et iusto odio dignissimos ducimus qui blanditiis praesentium voluptatum deleniti atque corrupti quos dolores et quas molestias excepturi sint occaecati cupiditate non provident, similique sunt in culpa qui officia deserun</p>

<div class="abs arrow" style="left:45px;background:#ddd;color:#fff">&#8592;</div>
<div class="abs arrow" style="left:1117px;background:#000;color:#fff">&#8594;</div>

<div class="abs card" style="left:111px">
  <div class="photo" role="img" aria-label="Pharmacist serving a customer at a counter" style="background:linear-gradient(135deg,#c9c2b8,#e8e4df 50%,#a9b8c6)"></div>
  <div class="icon"><div><svg width="40" height="40" viewBox="0 0 40 40" fill="none" stroke="#fff" stroke-width="2"><circle cx="20" cy="20" r="7"/><circle cx="20" cy="6" r="3"/><circle cx="20" cy="34" r="3"/><circle cx="6" cy="20" r="3"/><circle cx="34" cy="20" r="3"/><path d="M20 9v4M20 27v4M9 20h4M27 20h4"/></svg></div></div>
  <h3>Distribution</h3>
  <p>I must explain to you how all this mistaken idea of denouncing pleasure and praising pain was born and I will give you a complete</p>
  <a>View Details</a>
</div>
<div class="abs card" style="left:446px">
  <div class="photo" role="img" aria-label="Pharmacy aisle with stocked shelves" style="background:linear-gradient(135deg,#8fa3a6,#dfe6e4 50%,#9bb1a8)"></div>
  <div class="icon"><div><svg width="40" height="40" viewBox="0 0 40 40" fill="none" stroke="#fff" stroke-width="2"><rect x="12" y="6" width="12" height="5"/><rect x="10" y="11" width="16" height="22" rx="2"/><path d="M18 18v8M14 22h8"/><rect x="24" y="24" width="12" height="7" rx="3.5"/></svg></div></div>
  <h3>Pharma</h3>
  <p>I must explain to you how all this mistaken idea of denouncing pleasure and praising pain was born and I will give you a complete</p>
  <a>View Details</a>
</div>
<div class="abs card" style="left:780px">
  <div class="photo" role="img" aria-label="Operating room with capital medical equipment" style="background:linear-gradient(135deg,#6f7880,#c6ccd1 50%,#7d8891)"></div>
  <div class="icon"><div><svg width="40" height="40" viewBox="0 0 40 40" fill="none" stroke="#fff" stroke-width="2"><path d="M15 8h10M17 8v10L9 32h22L23 18V8"/><circle cx="28" cy="10" r="3"/><circle cx="33" cy="16" r="2"/></svg></div></div>
  <h3>Capital Equipment</h3>
  <p>I must explain to you how all this mistaken idea of denouncing pleasure and praising pain was born and I will give you a complete</p>
  <a>View Details</a>
</div>

<div class="abs quote-band"></div>
<div class="abs quote" style="top:2297px;color:var(--ink)">“WHERE TRANSPARENCY STARTS” -</div>
<div class="abs quote" style="top:2353px;color:var(--blue)">THE BRANTON &amp; KEEL GROUP</div>
<p class="abs lead" style="left:170px;width:860px;top:2425px;font:400 19px/31px 'Lato',sans-serif">At vero eos et accusamus et iusto odio dignissimos ducimus qui blanditiis praesentium voluptatum deleniti atque corrupti quos dolores et quas molestias excepturi sint occaecati cupiditate non p</p>
<div class="btn" style="left:540px;top:2508px;width:120px;height:40px">Get Started</div>

<svg class="abs" style="left:0;top:2570px" width="1200" height="513" viewBox="0 2570 1200 513">
  <path d="M100 2748 L948 2574 L1175 2755 L935 2618Z" fill="#0ba3e6"/>
  <path d="M0 2785 L935 2618 L1200 2787 L1200 3083 L0 3083Z" fill="#000"/>
</svg>
<svg class="abs" style="left:925px;top:2683px" width="12" height="12" viewBox="0 0 12 12" fill="none" stroke="#fff" stroke-width="2"><path d="M2 6l4-4 4 4M2 10l4-4 4 4"/></svg>
<div class="abs" style="left:886px;top:2706px;font:700 16px 'Lato',sans-serif;color:#fff">SCROLL UP</div>

<div class="abs" style="left:111px;top:2975px;font:700 25px 'Lato',sans-serif;color:#fff;display:flex;align-items:center;gap:10px"><span style="width:22px;height:22px;background:var(--blue);display:inline-block"></span>Brightpath Dental Supply</div>
<div class="abs footer-h" style="left:458px">USEFUL LINKS</div>
<ul class="abs links" style="left:460px;top:2841px"><li>Home</li><li>About Us</li><li>Areas of Practice</li><li>Reviews</li><li>Products</li></ul>
<ul class="abs links" style="left:640px;top:2843px"><li>Blogs</li><li>Solutions</li><li>Contact Us</li></ul>
<div class="abs footer-h" style="left:848px">GET IN TOUCH</div>
<div class="abs field" style="top:2853px">Full Name<span>&#9679;</span></div>
<div class="abs field" style="top:2903px">Email Address<span>&#9993;</span></div>
<div class="btn" style="left:848px;top:2953px;width:240px;height:36px;font-size:13px">Send Message</div>
<div class="abs" style="left:0;width:1200px;top:3045px;text-align:center;font:400 13px 'Lato',sans-serif;color:#fff">© 2023 Copyright | All Rights Reserved.</div>
</body>
</html>
```